Business Card Design Project

I require a business card with the following information on them for various different people;
name
m:
f:
e:
I have a logo already and will attached that. We are in the construction industry. I require something clean and simple but eye catching at the same time. You can use another colour with our logo if you like and you can style the logo as well if you wish. I am open.
Also it needs to be front and back design.
Industry/Entity Type
Construction
Requirements
Must have
- Logo, name, mobile, fax and email address.
Front and back design

```html
<!DOCTYPE html>
<html lang="en">
<head>
<meta charset="utf-8">
<title>Stonefield Developments – Business Card</title>
<link href="https://fonts.googleapis.com/css2?family=Arimo:wght@400&display=swap" rel="stylesheet">
<style>
  :root {
    --backdrop: #2a2a2a;
    --card: #ffffff;
    --green-dark: #0d4a26;
    --green-mid: #3f8f2a;
    --green-light: #7cc242;
    --grey-text: #6f6f6f;
    --grey-band: #b9b9b9;
    --ink: #111111;
  }
  * { box-sizing: border-box; margin: 0; padding: 0; }
  html, body {
    width: 1200px; height: 900px; overflow: hidden;
    background: var(--backdrop);
    font-family: "Arimo", Arial, sans-serif;
  }
  .stage {
    width: 1200px; height: 900px;
    display: flex; flex-direction: column; align-items: center; justify-content: center;
    gap: 34px;
  }
  .card {
    position: relative;
    width: 640px; height: 390px;
    background: var(--card);
    border-radius: 22px;
    overflow: hidden;
  }
  .card-art { position: absolute; inset: 0; width: 100%; height: 100%; }

  .brand {
    position: absolute;
    display: flex; align-items: center; gap: 12px;
    color: var(--green-light);
    font-size: 34px; font-weight: 400; letter-spacing: 0.5px;
    white-space: nowrap;
  }
  .brand-mark {
    width: 26px; height: 26px; background: var(--green-light);
  }
  .card-front .brand { left: 130px; top: 96px; }
  .card-back .brand { left: 50%; top: 128px; transform: translateX(-50%); font-size: 40px; }

  .holder-name {
    position: absolute; left: 24px; top: 222px;
    color: var(--green-light); font-size: 27px; font-weight: 400;
  }
  .contact-list {
    position: absolute; left: 24px; top: 266px;
    list-style: none; color: var(--ink); font-size: 16px;
  }
  .contact-list li { display: flex; align-items: center; gap: 7px; height: 25px; }
  .contact-row { display: flex; gap: 26px; }
  .contact-item { display: flex; align-items: center; gap: 7px; }
  .contact-list svg { width: 14px; height: 14px; fill: var(--green-light); flex: none; }
</style>
</head>
<body>
<main class="stage">

  <section class="card card-front" aria-label="Business card front">
    <svg class="card-art" viewBox="0 0 640 390" aria-hidden="true">
      <polygon points="360,272 640,228 640,244 350,284" fill="var(--grey-band)"/>
      <polygon points="0,368 640,262 640,298 0,404" fill="var(--green-dark)"/>
      <polygon points="150,380 640,302 640,314 170,390" fill="var(--green-light)"/>
      <line x1="20" y1="260" x2="360" y2="234" stroke="var(--ink)" stroke-width="1.5"/>
    </svg>

    <div class="brand"><span class="brand-mark"></span>Stonefield Developments</div>

    <h1 class="holder-name">Mark Fenton</h1>
    <ul class="contact-list">
      <li class="contact-row">
        <span class="contact-item">
          <svg viewBox="0 0 14 14"><rect x="3" y="0" width="8" height="14" rx="2"/><rect x="5" y="2" width="4" height="6" fill="#fff"/></svg>
          0400 218 574
        </span>
        <span class="contact-item">
          <svg viewBox="0 0 14 14"><rect x="0" y="5" width="14" height="7" rx="1"/><rect x="3" y="1" width="8" height="5" fill="none" stroke="var(--green-light)" stroke-width="1.5"/><rect x="2" y="7" width="3" height="3" fill="#fff"/></svg>
          03 9000 4521
        </span>
      </li>
      <li>
        <svg viewBox="0 0 14 14"><rect x="0" y="2" width="14" height="10" fill="none" stroke="var(--green-light)" stroke-width="1.5"/><polyline points="0,2 7,8 14,2" fill="none" stroke="var(--green-light)" stroke-width="1.5"/></svg>
        mark@stonefielddev.com.au
      </li>
    </ul>
  </section>

  <section class="card card-back" aria-label="Business card back">
    <svg class="card-art" viewBox="0 0 640 390" aria-hidden="true">
      <defs>
        <linearGradient id="back-band" x1="0" x2="1" y1="0" y2="0">
          <stop offset="0" stop-color="var(--green-dark)"/>
          <stop offset="0.5" stop-color="var(--green-light)"/>
          <stop offset="1" stop-color="var(--green-dark)"/>
        </linearGradient>
      </defs>
      <rect x="0" y="262" width="640" height="4" fill="var(--ink)"/>
      <rect x="0" y="282" width="640" height="50" fill="url(#back-band)"/>
    </svg>
    <div class="brand"><span class="brand-mark"></span>Stonefield Developments</div>
  </section>

</main>
</body>
</html>
```